Brellwick Partners, LLC Stationary

Brellwick Partners, LLC is a new financial planning and consulting company. We are looking for designs on business cards, letterhead, envelopes, and anything else that would be useful. Our preference for business card design is two sided. We are looking for a professional and clean look with incorporating the logo and patriotic feel. Thank you to all who participate and good luck!

```html
<!DOCTYPE html>
<html lang="en">
<head>
<meta charset="utf-8">
<title>Brellwick Partners, LLC – Business Card</title>
<link rel="stylesheet" href="https://fonts.googleapis.com/css2?family=Arimo:wght@400;700&display=swap">
<style>
  :root {
    --page-bg: #e9e7e3;
    --navy: #1d3d6b;
    --navy-deep: #152f55;
    --red: #c4222c;
    --red-deep: #8c1820;
    --white: #ffffff;
    --ink-soft: #dfe6f0;
  }
  * { box-sizing: border-box; margin: 0; padding: 0; }
  html, body {
    width: 1200px; height: 950px; overflow: hidden;
    background: var(--page-bg);
    font-family: "Arimo", Arial, sans-serif;
  }
  .sheet {
    width: 1200px; height: 950px;
    display: flex; flex-direction: column; align-items: center; justify-content: center;
    gap: 50px;
  }
  .card {
    position: relative;
    width: 700px; height: 400px;
    border-radius: 4px;
    overflow: hidden;
    box-shadow: 0 6px 18px rgba(0,0,0,.18);
  }

  /* Back side */
  .card-back {
    background: linear-gradient(160deg, var(--red) 0%, var(--red-deep) 100%);
    display: flex; flex-direction: column; align-items: center; justify-content: center;
    gap: 28px;
  }
  .brand { display: flex; align-items: center; gap: 16px; }
  .brand-mark { width: 34px; height: 34px; }
  .brand-name {
    font-weight: 700; font-size: 40px; letter-spacing: 1px;
    text-transform: uppercase;
  }
  .card-back .brand-mark { background: var(--white); }
  .card-back .brand-name { color: var(--white); }
  .back-web { color: var(--white); font-size: 18px; letter-spacing: 4px; }

  /* Front side */
  .card-front { background: var(--white); }
  .front-top {
    height: 178px;
    display: flex; align-items: center; justify-content: center;
    padding-left: 90px;
  }
  .card-front .brand-mark { background: var(--navy); }
  .card-front .brand-name { color: var(--navy); font-size: 36px; }
  .front-rule { height: 3px; background: var(--red); }
  .front-bottom {
    height: 219px;
    background: linear-gradient(180deg, var(--navy) 0%, var(--navy-deep) 100%);
    display: flex; justify-content: space-between;
    padding: 28px 40px 30px;
    color: var(--white);
  }
  .person-name { font-weight: 700; font-size: 22px; text-transform: uppercase; letter-spacing: .5px; }
  .person-title { font-size: 16px; text-transform: uppercase; margin-top: 4px; margin-bottom: 16px; }
  .address { font-size: 17px; line-height: 1.35; color: var(--ink-soft); }
  .contacts {
    list-style: none; align-self: flex-end;
    display: flex; flex-direction: column; align-items: flex-end; gap: 6px;
  }
  .contacts li { display: flex; align-items: center; gap: 10px; font-size: 17px; }
  .contacts svg { width: 16px; height: 16px; fill: var(--white); }
</style>
</head>
<body>
<main class="sheet">
  <section class="card card-back" aria-label="Business card back">
    <div class="brand">
      <span class="brand-mark"></span>
      <span class="brand-name">Brellwick Partners, LLC</span>
    </div>
    <p class="back-web">www.brellwick.com</p>
  </section>

  <section class="card card-front" aria-label="Business card front">
    <div class="front-top">
      <div class="brand">
        <span class="brand-mark"></span>
        <span class="brand-name">Brellwick Partners, LLC</span>
      </div>
    </div>
    <div class="front-rule"></div>
    <div class="front-bottom">
      <div class="person">
        <p class="person-name">Daniel Harlow</p>
        <p class="person-title">President</p>
        <p class="address">2718 Kestrel Avenue<br>Marlow Heights, NY 11207</p>
      </div>
      <ul class="contacts">
        <li>555 0147 2290
          <svg viewBox="0 0 16 16" aria-hidden="true"><path d="M3.5 1.5l2.5 0 1 3.5-1.6 1.2a9 9 0 0 0 4.4 4.4L11 9l3.5 1v2.5c0 1-1 2-2 2A12 12 0 0 1 1.5 3.5c0-1 1-2 2-2z"/></svg></li>
        <li>555 0183 6641
          <svg viewBox="0 0 16 16" aria-hidden="true"><rect x="4" y="1" width="8" height="5"/><rect x="1" y="6" width="14" height="6" rx="1"/><rect x="4" y="10" width="8" height="5"/></svg></li>
        <li>daniel@brellwick.com
          <svg viewBox="0 0 16 16" aria-hidden="true"><path d="M1 3h14v10H1z M1 3l7 6 7-6" stroke="#1d3d6b" stroke-width="1"/></svg></li>
        <li>www.brellwick.com
          <svg viewBox="0 0 16 16" aria-hidden="true"><circle cx="8" cy="8" r="7"/><path d="M6 5l5 3-5 3z" fill="#1d3d6b"/></svg></li>
      </ul>
    </div>
  </section>
</main>
</body>
</html>
```